QRV Advisors needs a web site

We need a web site for www.qrvadvisors-example.com. QRV is a mergers and acquisition consulting company that focuses our buyer and seller services on logistics companies. We help put companies together, and help with legal and financial due diligence. We want the web site to express our service and show the logistics components. We want personalized images versus pictures of trucks and airplanes.

Our new logo uses Burgandy and grey colors. Image attached. We are not in to bold, big letters...classy, artistic, low key preferred. Confidentiality, experience, professional are what we want to express on the site.

All we expect for the first part of this project is a home page, and one subpage.  We are budgeting other funds for the technical aspects of the web site

Reason: All that I'm seeing so far is trucks, forklifts and planes. We are a legal mergers and acquisitions firm that focus on logistics. I like some of the images to say logistics, but really want it say legal, financial, and putting companies together. Will pay extra for the sub page if someone can impress us with a home page.

Reason: Swamped with another project at the moment...will work on this over the weekend and provide designer feedback and select final design by Tuesday

```html
<!DOCTYPE html>
<html lang="en">
<head>
<meta charset="utf-8">
<title>QRV Advisors</title>
<link href="https://fonts.googleapis.com/css2?family=Open+Sans:wght@300;400;600;700&display=swap" rel="stylesheet">
<style>
:root{
  --burgundy:#a0093b;
  --ink:#333333;
  --muted:#555555;
  --soft:#8a8a8a;
  --band:#666666;
  --footer:#2f2f2f;
  --white:#ffffff;
}
*{margin:0;padding:0;box-sizing:border-box}
html,body{width:1002px;height:1200px;overflow:hidden;background:var(--white)}
body{position:relative;font-family:"Open Sans",Arial,sans-serif;color:var(--ink)}
h1,h2,h3,p{font-weight:inherit}
.abs{position:absolute}

.top-strip{left:0;top:0;width:1002px;height:42px;background:linear-gradient(90deg,#c98fd8,#d49ae0 50%,#cc8fdc)}
.top-band{left:0;top:42px;width:1002px;height:15px;background:var(--band)}

.site-header{left:0;top:57px;width:1002px;height:95px;background:var(--white)}
.brand{left:92px;top:87px;display:flex;align-items:center;gap:10px}
.brand-mark{width:14px;height:14px;background:var(--burgundy)}
.brand-name{font-size:25px;font-weight:400;color:var(--muted);letter-spacing:.5px}
.main-nav{right:199px;top:101px;display:flex;align-items:center;font-size:12px;color:var(--muted);text-transform:uppercase}
.main-nav .dot{width:4px;height:4px;border-radius:50%;background:var(--burgundy);margin:0 13px 0 14px}
.btn{background:var(--burgundy);color:var(--white);display:flex;align-items:center;justify-content:center;border-radius:3px}
.btn-contact{left:817px;top:94px;width:93px;height:28px;font-size:10.5px;font-weight:600}

.hero{left:0;top:152px;width:1002px;height:438px;
  background:linear-gradient(180deg,#b48ac2 0%,#c98466 24%,#b8764e 44%,#7a4a3a 62%,#2e2122 80%,#0e0a0a 100%)}
.hero-title{left:94px;top:472px;font-size:28px;font-weight:300;color:var(--white);letter-spacing:.2px}
.hero-text{left:94px;top:516px;width:690px;font-size:16.8px;line-height:24px;color:var(--white);font-weight:300}
.btn-hero{left:802px;top:529px;width:108px;height:34px;font-size:12px;font-weight:600}

.section-title{left:0;top:618px;width:978px;text-align:center;font-size:25px;font-weight:300;color:var(--burgundy)}
.card{position:absolute;top:675px;width:252px}
.card-image{width:242px;height:121px;box-shadow:0 1px 3px rgba(0,0,0,.25)}
.card-title{margin-top:10px;font-size:12.5px;font-weight:400;color:var(--burgundy);letter-spacing:-.3px}
.card-text{margin-top:6px;width:230px;font-size:9.8px;line-height:14.3px;color:var(--soft);font-weight:300}

.welcome-title{left:93px;top:910px;font-size:20px;font-weight:400;color:var(--ink)}
.welcome-text{left:91px;top:947px;width:535px;font-size:11.6px;line-height:23px;color:var(--muted);font-weight:300}
.btn-square{border-radius:0;font-size:11.5px}
.btn-welcome{left:91px;top:1081px;width:81px;height:26px}

.testimonials-title{left:691px;top:910px;font-size:21px;font-weight:300;color:var(--burgundy)}
.testimonial{position:absolute;left:694px;width:210px}
.avatar{width:47px;height:47px}
.quote{position:absolute;left:56px;top:-3px;width:142px;font-size:10.3px;line-height:15px;color:var(--muted);font-weight:300}
.author{position:absolute;left:56px;font-size:12px;font-weight:600;color:var(--burgundy);white-space:nowrap}
.btn-testimonials{left:692px;top:1107px;width:81px;height:24px}

.site-footer{left:0;top:1159px;width:1002px;height:41px;background:var(--footer)}
.copyright{left:93px;top:1172px;font-size:10.5px;color:#9a9a9a;font-weight:300}
.social-label{left:724px;top:1172px;font-size:10.5px;color:#9a9a9a;font-weight:300}
.social{top:1166px;width:26px;height:26px}
.social-a{left:822px;background:#2f5e9e}
.social-b{left:854px;background:#1f6fa8}
.social-c{left:886px;background:#2fa6dd}
</style>
</head>
<body>
  <div class="abs top-strip" role="img" aria-label="Photo strip of a city skyline at dusk"></div>
  <div class="abs top-band"></div>

  <header class="abs site-header"></header>
  <div class="abs brand">
    <span class="brand-mark"></span>
    <span class="brand-name">QRV Advisors</span>
  </div>
  <nav class="abs main-nav">
    <span>About QRV</span><span class="dot"></span>
    <span>Buyers</span><span class="dot"></span>
    <span>Due Diligence</span><span class="dot"></span>
    <span>Sellers</span>
  </nav>
  <a class="abs btn btn-contact">Contact Us Now</a>

  <section class="abs hero" role="img" aria-label="Photo of two advisors shaking hands across a boardroom table at dusk, a harbour faint through the window"></section>
  <h1 class="abs hero-title">Bringing Logistics Companies Together</h1>
  <p class="abs hero-text">Quiet, confidential counsel for buyers and sellers of logistics businesses. We guide each transaction from first meeting through legal and financial due diligence.</p>
  <a class="abs btn btn-hero">Read More Now</a>

  <h2 class="abs section-title">How We Advise</h2>

  <article class="card" style="left:100px">
    <div class="card-image" role="img" aria-label="Photo of an advisor meeting a buyer over documents" style="background:linear-gradient(160deg,#5a4a4e,#9a8a86 55%,#4a3a3e)"></div>
    <h3 class="card-title">Buyer Services</h3>
    <p class="card-text">We identify logistics firms that fit your plans and lead each approach with care and complete discretion.</p>
  </article>
  <article class="card" style="left:362px">
    <div class="card-image" role="img" aria-label="Photo of a business owner signing an agreement" style="background:linear-gradient(170deg,#cfc8c2,#9a8f88 55%,#5f5752)"></div>
    <h3 class="card-title">Seller Services</h3>
    <p class="card-text">We prepare your company for market and find the right partner to carry it forward.</p>
  </article>
  <article class="card" style="left:625px">
    <div class="card-image" role="img" aria-label="Photo of financial statements and a pen on a desk" style="background:linear-gradient(90deg,#a7a4a6,#e4e2e2 50%,#807b7e)"></div>
    <h3 class="card-title">Due Diligence</h3>
    <p class="card-text">Legal and financial review that brings clarity to every figure before the deal is closed.</p>
  </article>

  <h2 class="abs welcome-title">Welcome To QRV Advisors</h2>
  <p class="abs welcome-text">For many years we have advised owners and investors in the logistics sector on mergers and acquisitions. Every engagement is handled with strict confidentiality, and each client works directly with a senior partner who knows the industry and its people.<br>Our work joins legal insight with sound financial analysis, so that companies are brought together on terms that last and every party understands what it is signing.</p>
  <a class="abs btn btn-square btn-welcome">Read More</a>

  <h2 class="abs testimonials-title">Testimonials</h2>
  <div class="testimonial" style="top:956px">
    <div class="avatar" role="img" aria-label="Portrait of a client" style="background:linear-gradient(180deg,#d9cfc4,#b89a82)"></div>
    <p class="quote">Discreet, patient and precise. They guided our sale with great care.</p>
    <p class="author" style="top:46px">Marcus Ellery</p>
  </div>
  <div class="testimonial" style="top:1028px">
    <div class="avatar" role="img" aria-label="Portrait of a client" style="background:linear-gradient(180deg,#e6e1d8,#c7a98a)"></div>
    <p class="quote">Their due diligence gave us full confidence in the merger.</p>
    <p class="author" style="top:51px;left:58px">Marcus Ellery</p>
  </div>
  <a class="abs btn btn-square btn-testimonials">Read More</a>

  <footer class="abs site-footer"></footer>
  <p class="abs copyright">© Copyrights 2014 All rights Reserved</p>
  <p class="abs social-label">Socialize With Us :</p>
  <span class="abs social social-a" aria-label="Social network link"></span>
  <span class="abs social social-b" aria-label="Social network link"></span>
  <span class="abs social social-c" aria-label="Social network link"></span>
</body>
</html>
```